Menu Board and Flyer for a Poke Restaurant

We need for our new Menu board for a Poke restaurant. There will be 2 separate boards. 1 Board for Speciality items, the second for "Build your Own". The menu boards will be installed on a wall.

The first board is going to be 36 W x 48 H inches. The second board will be 72 W x 48 H inches.

I would also like to consolidate the board into a one Page menu flyer that can be printed on an 11 inches x 14 inches Page.

The goal is to have customers focus on the ease of ordering.
We have attached a sample design idea for reference and our logo options. Including the logo is optional.

I have included some sample menus by other companies as attachment and referance.

Files need to include any special fonts used in the design.

Target Market(s)

Young Professionals who love eating healthy, trendy, delicious new food options.

Industry/Entity Type

Fast Food Restaurant

Font styles to use
Serif
Sans Serif

Requirements
Must have
• Simple
• Clean design - NOT busy
• Fun
• Easy to follow
• Highlight a step by step ordering process.
• Light background color
• Files need to include any special fonts used in the design.
Should not have
• script fonts

```html
<!DOCTYPE html>
<html lang="en">
<head>
<meta charset="utf-8">
<title>House Specialties Menu</title>
<link rel="stylesheet" href="https://fonts.googleapis.com/css2?family=Antonio:wght@100;300;400&family=Poppins:wght@500&family=Questrial&display=swap">
<style>
  :root {
    --page-bg: #e9e7e3;
    --card-bg: #ffffff;
    --ink: #111111;
    --ink-soft: #3a3a3a;
    --rule: #222222;
  }
  * { margin: 0; padding: 0; box-sizing: border-box; }
  html, body { width: 1200px; height: 1000px; overflow: hidden; }
  body { background: var(--page-bg); position: relative; }

  .menu-card {
    position: absolute; left: 265px; top: 42px;
    width: 672px; height: 896px;
    background: var(--card-bg);
    color: var(--ink);
    box-shadow: 0 2px 8px rgba(0,0,0,0.12);
  }
  .menu-card > * { position: absolute; }

  .menu-title {
    left: 26px; top: 38px;
    font-family: "Questrial", sans-serif;
    font-size: 46px; letter-spacing: 1px; line-height: 1;
  }

  .brand { left: 452px; top: 118px; display: flex; align-items: center; gap: 10px; }
  .brand-dot { width: 16px; height: 16px; border: 2px solid var(--ink); border-radius: 50%; }
  .brand-name { font-family: "Questrial", sans-serif; font-size: 22px; color: var(--ink); white-space: nowrap; }

  .step-number {
    font-family: "Antonio", sans-serif; font-weight: 400;
    font-size: 118px; line-height: 1;
  }
  .step-kicker {
    font-family: "Antonio", sans-serif; font-weight: 300;
    font-size: 14px; letter-spacing: 1.5px; color: var(--ink-soft); line-height: 1;
  }
  .step-heading {
    font-family: "Antonio", sans-serif; font-weight: 400;
    font-size: 42px; line-height: 1; letter-spacing: 0.5px;
  }
  .rule { background: var(--rule); }

  .option-grid { display: grid; }
  .option {
    font-family: "Antonio", sans-serif; font-weight: 100;
    font-size: 25px; letter-spacing: 2px; color: var(--ink-soft);
    line-height: 33px; text-transform: uppercase; white-space: nowrap;
  }
  .style-name {
    font-family: "Poppins", sans-serif; font-weight: 500;
    font-size: 24px; line-height: 30px; color: var(--ink);
  }

  /* step 1 */
  .step-1-number { left: 72px; top: 150px; }
  .step-1-kicker { left: 110px; top: 157px; }
  .step-1-rule { left: 205px; top: 165px; width: 230px; height: 1px; }
  .step-1-heading { left: 110px; top: 172px; }
  .step-1-box {
    left: 118px; top: 226px; width: 427px; height: 112px;
    border: 1px solid var(--rule); border-top: none;
  }
  .specialty-list { left: 135px; top: 228px; grid-template-columns: 197px 197px; }

  /* step 2 */
  .step-2-box {
    left: 118px; top: 383px; width: 427px; height: 259px;
    border: 1px solid var(--rule);
  }
  .step-2-mask { left: 440px; top: 360px; width: 140px; height: 90px; background: var(--card-bg); }
  .step-2-kicker { left: 448px; top: 362px; }
  .step-2-heading { left: 448px; top: 375px; }
  .step-2-number { left: 552px; top: 368px; font-size: 96px; }
  .style-list { left: 144px; top: 420px; grid-template-columns: 176px 200px; row-gap: 10px; }
  .style-item .option { line-height: 33px; }

  /* step 3 */
  .step-3-number { left: 72px; top: 680px; }
  .step-3-kicker { left: 115px; top: 688px; }
  .step-3-heading { left: 115px; top: 703px; }
  .step-3-box {
    left: 118px; top: 707px; width: 427px; height: 111px;
    border: 1px solid var(--rule);
  }
  .step-3-mask { left: 112px; top: 700px; width: 92px; height: 14px; background: var(--card-bg); }
  .base-list { left: 221px; top: 739px; grid-template-columns: 173px 173px; }
</style>
</head>
<body>
  <main class="menu-card">
    <h1 class="menu-title">HOUSE SPECIALTIES</h1>

    <div class="brand">
      <span class="brand-dot"></span>
      <span class="brand-name">Harbor Poke House</span>
    </div>

    <!-- Step 1 -->
    <div class="step-1-box"></div>
    <div class="step-number step-1-number">1</div>
    <div class="step-kicker step-1-kicker">CHOOSE A</div>
    <div class="rule step-1-rule"></div>
    <h2 class="step-heading step-1-heading">SPECIALTY</h2>
    <ul class="option-grid specialty-list" style="list-style:none">
      <li class="option">Lava Hot</li>
      <li class="option">Crazy Kimchi</li>
      <li class="option">Classic Hawaiian</li>
      <li class="option">Wasabi Lover</li>
      <li class="option">Sweet and Spicy</li>
      <li class="option">Ginger Ginger</li>
    </ul>

    <!-- Step 2 -->
    <div class="step-2-box"></div>
    <div class="step-2-mask"></div>
    <div class="step-kicker step-2-kicker">CHOOSE YOUR</div>
    <h2 class="step-heading step-2-heading">STYLE</h2>
    <div class="step-number step-2-number">2</div>
    <div class="option-grid style-list">
      <div class="style-item">
        <div class="style-name">classic bowl</div>
        <div class="option">Regular or<br>Large</div>
      </div>
      <div class="style-item">
        <div class="style-name">crunchy bowl</div>
        <div class="option">One size,<br>Tostada style</div>
      </div>
      <div class="style-item">
        <div class="style-name">surfer style</div>
        <div class="option">Poke served<br>Taco style</div>
      </div>
      <div class="style-item">
        <div class="style-name">just poke</div>
        <div class="option">No base, 1lb of<br>your favorite poke</div>
      </div>
    </div>

    <!-- Step 3 -->
    <div class="step-3-box"></div>
    <div class="step-3-mask"></div>
    <div class="step-number step-3-number">3</div>
    <div class="step-kicker step-3-kicker">CHOOSE YOUR</div>
    <h2 class="step-heading step-3-heading">BASE</h2>
    <ul class="option-grid base-list" style="list-style:none">
      <li class="option">White Rice</li>
      <li class="option">Brown Rice</li>
      <li class="option">Black Rice</li>
      <li class="option">Mixed Greens</li>
    </ul>
  </main>
</body>
</html>
```